Business Card for Multi-Brand Sportswear Company

We are looking for a business card which represents our company and the multiple brands within it.

The company: Fen Athletics (LTD)
The brands: Fen, TavaPuni, ElmStretch, Grit and Rain

Employees using these cards would be representing Fen Athletics, rather than any of the individual brands. You will see a current design within the uploaded files, to give some inspiration. The actual text of the brands is not necessary, but the logos should be on there is some format.

Our creative minds on this are stretched, so we are looking for someone to make this their own, and show us what a good business card should look like.

We may like to get these printed with spot gloss, so keep that in mind with your designs.

www.fenathletics.co.uk

Industry/Entity Type

Business

Contact Information for Business Card

Leo Pemberton-Hale
Operations Manager
(+44) 1632 960 418
Leo@fenathletics.co.uk
www.fenathletics.co.uk

Font styles to use
Sans Serif
Other font styles liked:
• Eurostile

Colors
ffffff

Requirements
Nice to have
• Dark (black) background

```html
<!DOCTYPE html>
<html lang="en">
<head>
<meta charset="utf-8">
<title>Fen Athletics – Business Card</title>
<link rel="stylesheet" href="https://fonts.googleapis.com/css2?family=Michroma&family=Roboto:wght@400;500&display=swap">
<style>
  :root {
    --stage: #2a2a2b;
    --card: #0b0b0c;
    --white: #ffffff;
    --silver: #c9c9cc;
    --red: #e3202a;
    --muted: #b9b9bd;
  }
  * { margin: 0; padding: 0; box-sizing: border-box; }
  html, body { width: 1200px; height: 900px; overflow: hidden; background: var(--stage); }
  .canvas { position: relative; width: 1200px; height: 900px; }
  .card {
    position: absolute; width: 620px; height: 354px;
    background: var(--card); overflow: hidden;
    box-shadow: 0 18px 40px rgba(0,0,0,.55);
  }
  .card svg.shapes { position: absolute; inset: 0; }
  .card-front { left: 70px; top: 80px; }
  .card-back { left: 510px; top: 466px; }

  .wordmark { position: absolute; font-family: "Michroma", sans-serif; color: var(--silver); }
  .front-wordmark { left: 150px; top: 112px; font-size: 40px; letter-spacing: 2px; }
  .front-tagline {
    position: absolute; left: 346px; top: 166px;
    font-family: "Roboto", sans-serif; font-size: 10px; letter-spacing: 3px; color: var(--muted);
  }

  .back-wordmark { right: 40px; top: 40px; font-size: 44px; color: var(--silver); }
  .identity { position: absolute; right: 40px; top: 112px; text-align: right; font-family: "Roboto", sans-serif; }
  .identity .name { font-family: "Michroma", sans-serif; font-size: 15px; color: var(--white); }
  .identity .role { font-size: 14px; color: var(--red); margin-top: 3px; }
  .identity .rule { height: 1px; background: var(--red); width: 300px; margin: 4px 0 4px auto; }
  .identity .address { font-size: 13px; color: var(--white); line-height: 1.3; }

  .brand-row { position: absolute; left: 26px; top: 212px; display: flex; gap: 16px; align-items: center; }
  .brand { display: flex; align-items: center; gap: 5px; font-family: "Roboto", sans-serif; font-size: 11px; font-weight: 500; color: var(--silver); }
  .brand .dot { width: 9px; height: 9px; border-radius: 50%; background: var(--red); }
  .brand .square { width: 9px; height: 9px; background: var(--silver); }

  .contact-rule { position: absolute; left: 26px; top: 240px; width: 220px; height: 1px; background: var(--red); }
  .contacts { position: absolute; left: 26px; top: 248px; list-style: none; font-family: "Roboto", sans-serif; font-size: 14px; color: var(--white); }
  .contacts li { display: flex; align-items: center; gap: 8px; line-height: 21px; }
  .contacts svg { width: 12px; height: 12px; }
</style>
</head>
<body>
<main class="canvas">

  <section class="card card-front" aria-label="Card front">
    <svg class="shapes" viewBox="0 0 620 354" width="620" height="354">
      <polygon points="0,270 300,270 330,248 620,218 620,234 342,262 316,330 0,330" fill="var(--white)"/>
      <polygon points="330,250 356,247 350,258 324,261" fill="var(--red)"/>
      <polygon points="362,246 388,243 382,254 356,257" fill="var(--red)"/>
      <polygon points="394,242 420,239 414,250 388,253" fill="var(--red)"/>
    </svg>
    <div class="wordmark front-wordmark">FEN ATHLETICS</div>
    <div class="front-tagline">PERFORMANCE WEAR</div>
  </section>

  <section class="card card-back" aria-label="Card back">
    <svg class="shapes" viewBox="0 0 620 354" width="620" height="354">
      <polygon points="450,200 620,172 620,232 440,262" fill="var(--red)"/>
      <polygon points="0,354 0,324 340,280 620,232 620,354" fill="var(--card)"/>
      <polygon points="0,340 320,290 330,300 0,354" fill="var(--red)"/>
      <polygon points="330,298 620,250 620,262 336,308" fill="var(--red)"/>
      <polygon points="372,256 388,254 382,278 366,280" fill="var(--white)"/>
      <polygon points="396,252 412,250 406,274 390,276" fill="var(--white)"/>
      <polygon points="420,248 436,246 430,270 414,272" fill="var(--white)"/>
    </svg>

    <div class="wordmark back-wordmark">Fen</div>

    <div class="identity">
      <div class="name">Leo Pemberton-Hale</div>
      <div class="rule"></div>
      <div class="role">Operations Manager</div>
      <div class="address">Hollow Lane, Ashby<br>Fenwick, YO9 4PX</div>
    </div>

    <div class="brand-row">
      <span class="brand"><span class="square"></span>TavaPuni</span>
      <span class="brand">Grit and Rain</span>
      <span class="brand"><span class="dot"></span>ElmStretch</span>
    </div>

    <div class="contact-rule"></div>
    <ul class="contacts">
      <li>
        <svg viewBox="0 0 12 12" aria-hidden="true"><circle cx="6" cy="6" r="6" fill="var(--red)"/><path d="M4 3.5l1 1-.6.8a4 4 0 002.3 2.3l.8-.6 1 1-.8.8C5.8 8.6 3.4 6.2 3.2 4.3z" fill="var(--white)"/></svg>
        (+44) 1632 960 418
      </li>
      <li>
        <svg viewBox="0 0 12 12" aria-hidden="true"><circle cx="6" cy="6" r="6" fill="var(--red)"/><rect x="3" y="4" width="6" height="4" fill="none" stroke="var(--white)" stroke-width=".8"/><path d="M3 4l3 2.2L9 4" fill="none" stroke="var(--white)" stroke-width=".8"/></svg>
        Leo@fenathletics.co.uk
      </li>
      <li>
        <svg viewBox="0 0 12 12" aria-hidden="true"><circle cx="6" cy="6" r="6" fill="var(--red)"/><circle cx="6" cy="6" r="3" fill="none" stroke="var(--white)" stroke-width=".8"/><path d="M3 6h6M6 3v6" stroke="var(--white)" stroke-width=".6"/></svg>
        www.fenathletics.co.uk
      </li>
    </ul>
  </section>

</main>
</body>
</html>
```